Website Design for The Elder Nook

Please design and code a new website.
Here are the sites I like best:
http://www.voyaglint.com/alternate/
http://www.wheelgiftbay.org
Please make it similar but look at the competitor site (below) for images and wording. This is NOT a car donation site. It's a senior lead placement site like https://www.kinhavenfinder.com. I just like this sites above as a lead generation sites.
Competitor site:
https://www.kinhavenfinder.com (use ideas / verbiage from this site)
Updates
Competitor site:
Coding
Coded - Design and coding required
Number of Pages Required
1 page
Look and feel
Each slider illustrates characteristics of the customer's brand and the style your logo design should communicate.

```html
<!DOCTYPE html>
<html lang="en">
<head>
<meta charset="utf-8">
<title>The Elder Nook — Senior Living Advisors</title>
<link rel="stylesheet" href="https://fonts.googleapis.com/css2?family=Montserrat:ital,wght@0,400;0,500;0,600;0,700;0,800;1,500&display=swap">
<style>
:root{
  --navy:#1d2566;
  --navy-deep:#161c4f;
  --indigo:#2f2a78;
  --green:#14a05a;
  --green-dark:#0e8a4c;
  --ink:#1e1e2a;
  --muted:#4a4a58;
  --line:#d9dce6;
  --paper:#ffffff;
  --mist:#f1f3f7;
}
*{box-sizing:border-box;margin:0;padding:0}
html,body{width:1200px;height:5128px;overflow:hidden}
body{font-family:'Montserrat',sans-serif;color:var(--ink);background:var(--paper);position:relative}
section,header,footer,nav{position:absolute;left:0;width:1200px}
.abs{position:absolute}
.brand{display:flex;align-items:center;gap:12px}
.brand-dot{width:34px;height:34px;border-radius:50%;background:var(--green)}
.brand-name{font-size:30px;font-weight:700;color:var(--navy)}
.brand-tag{font-size:10px;font-weight:600;letter-spacing:1px;color:var(--muted);margin-top:4px;padding-left:46px}
.btn{display:inline-block;background:var(--green);color:#fff;font-weight:700;border-radius:3px}
.section-title{width:100%;text-align:center;font-size:32px;font-weight:700;color:var(--navy)}
.section-title em{font-style:normal;color:var(--green)}
ul{list-style:none}

/* header */
.site-header{top:0;height:130px;background:#fff}
.site-header .brand{position:absolute;left:40px;top:30px}
.header-phone{position:absolute;right:60px;top:30px;display:flex;align-items:center;gap:12px}
.phone-ring{width:56px;height:56px;border-radius:50%;border:3px solid var(--navy);display:flex;align-items:center;justify-content:center}
.header-phone strong{display:block;font-size:30px;font-weight:800;color:var(--navy);line-height:1}
.header-phone small{font-size:11px;color:var(--muted)}
.main-nav{top:130px;height:36px;background:var(--navy-deep);display:flex;align-items:center;padding-left:40px;gap:28px}
.main-nav a{color:#fff;font-size:12px;font-weight:700;text-decoration:none;letter-spacing:.3px}

/* hero */
.hero{top:166px;height:466px}
.hero-photo{position:absolute;inset:0;background:linear-gradient(100deg,#7f9a6b 0%,#b9c7a4 35%,#d9ddd0 55%,#8fa77e 80%,#5e7d4f 100%)}
.lead-form{position:absolute;left:806px;top:0;width:360px;height:382px;background:var(--navy)}
.lead-form .form-head{background:#fff;padding:16px 20px;text-align:center;font-size:17px;font-weight:700;color:var(--navy);line-height:1.3}
.lead-form .form-head em{font-style:normal;color:var(--green)}
.field{margin:9px 24px 0;height:34px;background:#fff;border-radius:2px;font-size:12px;font-weight:600;color:#333;padding:9px 10px;position:relative}
.field.select::after{content:"";position:absolute;right:12px;top:14px;border:6px solid transparent;border-top-color:var(--navy)}
.lead-form .btn{margin:14px 24px 0;padding:10px 22px;font-size:13px}

/* support band */
.support{top:632px;height:188px;background:var(--green)}
.support-title{position:absolute;left:0;top:0;width:480px;height:188px;background:var(--navy);clip-path:polygon(0 0,100% 0,88% 100%,0 100%);padding:48px 0 0 118px;color:#fff;font-size:22px;font-weight:800;line-height:1.2}
.support-title span{font-size:35px;display:block}
.perk{position:absolute;top:36px;width:120px;text-align:center;color:#fff;font-size:13px;font-weight:700;line-height:1.25}
.perk svg{display:block;margin:0 auto 12px}

/* steps */
.steps{top:820px;height:600px}
.steps .section-title{position:absolute;top:130px}
.step{position:absolute;top:200px;width:220px;text-align:center}
.step .step-photo{width:170px;height:170px;border-radius:50%;margin:0 auto;border:5px solid #e7e9ef;background:radial-gradient(circle at 45% 40%,#e9d6c4,#b7a08c 60%,#8f9aa8)}
.step b{display:block;margin-top:26px;font-size:22px;font-weight:800;color:var(--navy)}
.step p{font-size:17px;font-weight:500;color:var(--ink);line-height:1.3;margin-top:4px}

/* no cost */
.no-cost{top:1420px;height:362px;background:var(--mist)}
.no-cost-photo{position:absolute;left:0;top:0;width:640px;height:362px;background:linear-gradient(90deg,#c9b7a5 0%,#e6dcd2 55%,rgba(241,243,247,0) 100%)}
.no-cost-copy{position:absolute;left:720px;top:92px;width:420px}
.no-cost-copy h2{font-size:34px;font-weight:800;color:var(--navy)}
.no-cost-copy h2 em{font-style:normal;color:var(--green)}
.no-cost-copy p{font-size:15px;font-weight:700;line-height:1.45;margin-top:16px;text-align:center}
.no-cost-copy .btn{margin:20px 0 0 40px;padding:14px 20px;font-size:29px;font-weight:800}

/* veterans */
.veterans{top:1900px;height:320px}
.veterans h2{position:absolute;left:95px;top:20px;font-size:23px;font-weight:800;color:var(--navy)}
.veterans h2 em{font-style:normal;color:var(--green)}
.veterans p{position:absolute;left:95px;top:105px;width:560px;font-size:17px;line-height:1.5;color:var(--ink)}
.veterans .btn{position:absolute;left:95px;top:262px;padding:11px 40px;font-size:15px;font-weight:600}
.vet-photo{position:absolute;left:805px;top:58px;width:200px;height:200px;border-radius:50%;background:linear-gradient(135deg,#c5ccd8 0%,#7d8fb5 45%,#b43a44 75%,#e7e9ef 100%)}

/* testimonials */
.testimonials{top:2325px;height:330px;background:linear-gradient(180deg,#3a3488,#2d2872)}
.testimonials .section-title{position:absolute;top:52px;color:#fff}
.quote{position:absolute;top:135px;width:300px;color:#fff}
.quote p{font-size:12px;line-height:1.45;padding-left:34px;padding-right:60px;position:relative;opacity:.95}
.quote p::before{content:"\201C";position:absolute;left:0;top:-14px;font-size:56px;font-weight:800;color:var(--green);line-height:1}
.quote p::after{content:"\201D";position:absolute;right:30px;bottom:-36px;font-size:56px;font-weight:800;color:var(--green);line-height:1}
.quote .avatar{position:absolute;right:0;top:64px;width:60px;height:60px;border-radius:50%;border:3px solid #fff;background:linear-gradient(135deg,#d9c6b2,#8b98ad)}
.quote cite{display:block;margin-top:34px;font-size:15px;font-weight:500;font-style:italic}
.dots{position:absolute;top:300px;left:568px;display:flex;gap:8px}
.dots i{width:10px;height:10px;border-radius:50%;border:1.5px solid #fff}
.dots i.on{background:#fff}

/* states */
.states{top:2700px;height:620px}
.states .section-title{position:absolute;top:60px}
.care-tabs{position:absolute;left:95px;top:150px;width:270px}
.care-tabs li{height:60px;margin-bottom:10px;border:1px solid var(--line);display:flex;align-items:center;gap:20px;font-size:16px;font-weight:600;color:var(--ink);position:relative;background:#fff}
.care-tabs li .tab-icon{width:52px;height:58px;background:var(--navy);display:flex;align-items:center;justify-content:center}
.care-tabs li.active{color:var(--green)}
.care-tabs li.active .tab-icon{background:var(--green)}
.care-tabs li.active::after{content:"";position:absolute;right:14px;top:23px;border:7px solid transparent;border-right-color:var(--green)}
.state-col{position:absolute;top:150px;font-size:15px;line-height:25.5px;color:var(--ink)}

/* advisor */
.advisor{top:3455px;height:450px;background:linear-gradient(90deg,#ffffff 0%,#f4f7fb 40%,#cfe0ef 60%,#9fc0de 100%)}
.advisor-photo{position:absolute;left:620px;top:0;width:580px;height:450px;background:radial-gradient(ellipse at 55% 55%,#e8eef4 0%,#b6cbe0 45%,rgba(159,192,222,0) 75%)}
.advisor h2{position:absolute;left:95px;top:60px;font-size:34px;font-weight:800;color:var(--navy);line-height:1.25}
.advisor h2 em{font-style:normal;color:var(--green);display:block}
.advisor .lead{position:absolute;left:95px;top:170px;width:440px;font-size:16px;font-weight:600;line-height:1.45}
.advisor ul{position:absolute;left:95px;top:255px}
.advisor li{display:flex;align-items:center;gap:16px;font-size:16px;font-weight:700;height:44px}

/* city links */
.city-links{top:4020px;height:560px}
.city-col{position:absolute;top:0;width:380px}
.city-col h3{font-size:19px;font-weight:800;color:var(--navy);margin-bottom:28px}
.city-col li{font-size:15px;line-height:25.5px;color:var(--ink)}

/* footer */
.site-footer{top:4668px;height:400px;background:linear-gradient(180deg,#262b72,#1a1f58)}
.site-footer .brand{position:absolute;left:470px;top:40px}
.site-footer .brand-name{color:#fff}
.site-footer .brand-tag{position:absolute;left:470px;top:92px;color:#c8cbe6}
.foot-col{position:absolute;top:178px;color:#fff}
.foot-col h4{font-size:12px;font-weight:700;letter-spacing:.6px;color:var(--green);margin-bottom:14px}
.foot-col p{font-size:12px;line-height:1.5;width:230px}
.foot-col li{font-size:12px;line-height:1.55}
.foot-phone{position:absolute;left:810px;top:172px;display:flex;gap:12px;align-items:center;color:#fff}
.foot-phone .phone-ring{border-color:#fff}
.foot-phone strong{display:block;font-size:29px;font-weight:800;line-height:1}
.foot-phone small{font-size:11px}
.socials{position:absolute;left:880px;top:250px;display:flex;gap:10px}
.socials span{width:30px;height:30px;background:var(--green);border-radius:3px}
.copyright{top:5068px;height:60px;background:#fff;text-align:center;font-size:11px;font-weight:700;line-height:60px;color:var(--ink)}
</style>
</head>
<body>

<header class="site-header">
  <div class="brand"><span class="brand-dot"></span><span class="brand-name">The Elder Nook</span></div>
  <div class="brand-tag abs" style="left:40px;top:72px">CONNECTING FAMILIES TO SENIOR LIVING</div>
  <div class="header-phone">
    <span class="phone-ring"><svg width="26" height="26" viewBox="0 0 24 24"><path d="M6.6 10.8a15 15 0 0 0 6.6 6.6l2.2-2.2a1 1 0 0 1 1-.25 11.4 11.4 0 0 0 3.6.57 1 1 0 0 1 1 1V20a1 1 0 0 1-1 1A17 17 0 0 1 3 4a1 1 0 0 1 1-1h3.5a1 1 0 0 1 1 1c0 1.25.2 2.45.57 3.6a1 1 0 0 1-.25 1z" fill="#1d2566"/></svg></span>
    <div><strong>1-800-555-0142</strong><small>Call Today to a Local Advisor for FREE</small></div>
  </div>
</header>

<nav class="main-nav">
  <a>ASSISTED LIVING</a><a>MEMORY CARE</a><a>NURSING HOMES</a><a>MORE LIVING OPTIONS ▾</a><a>PLANNING &amp; ADVICE</a>
</nav>

<section class="hero">
  <div class="hero-photo" role="img" aria-label="Senior couple walking together along a leafy park path"></div>
  <form class="lead-form">
    <div class="form-head">You know your family. We know<br><em>Senior Living. Contact us now!</em></div>
    <div class="field">First Name*</div>
    <div class="field">Last Name*</div>
    <div class="field">Primary Phone*</div>
    <div class="field">Cell Phone*</div>
    <div class="field">Email*</div>
    <div class="field select">State*</div>
    <span class="btn">SUBMIT</span>
  </form>
</section>

<section class="support">
  <h2 class="support-title">THE SUPPORT YOU<br>NEED TO MAKE THE<span>RIGHT CHOICE</span></h2>
  <div class="perk" style="left:453px">
    <svg width="54" height="54" viewBox="0 0 54 54" fill="none" stroke="#fff" stroke-width="3"><circle cx="27" cy="18" r="9"/><path d="M10 48c0-10 8-16 17-16s17 6 17 16"/></svg>Dedicated local advisor</div>
  <div class="perk" style="left:572px">
    <svg width="54" height="54" viewBox="0 0 54 54" fill="none" stroke="#fff" stroke-width="3"><path d="M6 48V26L20 14l14 12v22zM34 48V20l8-6 8 6v28"/><rect x="15" y="34" width="10" height="14"/></svg>Hand-picked list of communities</div>
  <div class="perk" style="left:685px">
    <svg width="54" height="54" viewBox="0 0 54 54" fill="none" stroke="#fff" stroke-width="3"><rect x="12" y="6" width="30" height="42" rx="2"/><rect x="17" y="11" width="20" height="9"/><path d="M18 28h4M26 28h4M34 28h2M18 35h4M26 35h4M34 35h2M18 42h4M26 42h4"/></svg>Full details and pricing</div>
  <div class="perk" style="left:805px">
    <svg width="54" height="54" viewBox="0 0 54 54" fill="none" stroke="#fff" stroke-width="3"><rect x="8" y="10" width="38" height="38" rx="2"/><path d="M8 20h38M17 5v10M37 5v10M16 28h6M25 28h6M34 28h4M16 38h6M25 38h6"/></svg>Help scheduling tours</div>
  <div class="perk" style="left:983px">
    <svg width="54" height="54" viewBox="0 0 54 54" fill="none" stroke="#fff" stroke-width="3"><path d="M6 34l5-12h32l5 12v8H6z"/><circle cx="15" cy="42" r="4"/><circle cx="39" cy="42" r="4"/></svg>Move in support</div>
</section>

<section class="steps">
  <h2 class="section-title">How Our <em>Service Works</em></h2>
  <div class="step" style="left:130px"><div class="step-photo" role="img" aria-label="Smiling advisor wearing a headset"></div><b>01.</b><p>Talk with your<br>local advisor</p></div>
  <div class="step" style="left:383px"><div class="step-photo" role="img" aria-label="Family reviewing care options together"></div><b>02.</b><p>Get information<br>on care options</p></div>
  <div class="step" style="left:597px"><div class="step-photo" role="img" aria-label="Family visiting a senior community"></div><b>03.</b><p>Select communities<br>to visit</p></div>
  <div class="step" style="left:850px"><div class="step-photo" role="img" aria-label="Senior settling into a new home"></div><b>04.</b><p>Transition to<br>new home</p></div>
</section>

<section class="no-cost">
  <div class="no-cost-photo" role="img" aria-label="Grandmother and granddaughter embracing"></div>
  <div class="no-cost-copy">
    <h2>There's <em>No Cost</em> to You</h2>
    <p>We work with over 20,000 senior living communities. Our community partners pay us for placement services.</p>
    <span class="btn">Call 1-800-555-0142</span>
  </div>
</section>

<section class="veterans">
  <h2>Access up to $2,000 per Month <em>in Veteran's Aid</em></h2>
  <p>We work with Veterans every day. Most veteran families do not know of a key benefit available to them and their families. It's called the Veteran's Aid and Attendance benefit. This benefit can help pay for senior living and home care.</p>
  <span class="btn">Learn More</span>
  <div class="vet-photo" role="img" aria-label="Veteran saluting in front of a national flag"></div>
</section>

<section class="testimonials">
  <h2 class="section-title">97% of Our Customers Recommend Our Service</h2>
  <blockquote class="quote" style="left:95px"><p>Lorem ipsum dolor sit amet, con sectetuer adipiscing elit, sed diam nonummy nibh euismod tincidunt ut laoreet dolore magna aliquam er at volu.</p><span class="avatar" role="img" aria-label="Customer portrait"></span><cite>Marla Quinby</cite></blockquote>
  <blockquote class="quote" style="left:445px"><p>Lorem ipsum dolor sit amet, con sectetuer adipiscing elit, sed diam nonummy nibh euismod tincidunt ut laoreet dolore magna aliquam er at volu.</p><span class="avatar" role="img" aria-label="Customer portrait"></span><cite>Dorian Vale</cite></blockquote>
  <blockquote class="quote" style="left:795px"><p>Lorem ipsum dolor sit amet, con sectetuer adipiscing elit, sed diam nonummy nibh euismod tincidunt ut laoreet dolore magna aliquam er at volu.</p><span class="avatar" role="img" aria-label="Customer portrait"></span><cite>Tobias Renfrew</cite></blockquote>
  <div class="dots"><i class="on"></i><i></i><i></i><i></i></div>
</section>

<section class="states">
  <h2 class="section-title">Senior Living <em>by State</em></h2>
  <ul class="care-tabs">
    <li class="active"><span class="tab-icon"><svg width="26" height="26" viewBox="0 0 24 24" fill="#fff"><circle cx="8" cy="5" r="3"/><circle cx="16" cy="5" r="3"/><path d="M4 10h8v12H4zM12 10h8v12h-8z" opacity=".9"/></svg></span>Assisted Living</li>
    <li><span class="tab-icon"><svg width="26" height="26" viewBox="0 0 24 24" fill="none" stroke="#fff" stroke-width="2"><circle cx="12" cy="10" r="7"/><path d="M9 22h6"/></svg></span>Memory Care</li>
    <li><span class="tab-icon"><svg width="26" height="26" viewBox="0 0 24 24" fill="#fff"><circle cx="12" cy="5" r="3"/><path d="M8 10h8l-1 12H9z"/></svg></span>Independent Living</li>
    <li><span class="tab-icon"><svg width="26" height="26" viewBox="0 0 24 24" fill="#fff"><path d="M10 3h4v7h7v4h-7v7h-4v-7H3v-4h7z"/></svg></span>Nursing Home</li>
    <li><span class="tab-icon"><svg width="26" height="26" viewBox="0 0 24 24" fill="#fff"><path d="M12 3l9 8h-3v10H6V11H3z"/></svg></span>Care Homes</li>
  </ul>
  <ul class="state-col" style="left:450px"><li>Alabama</li><li>Arizona</li><li>Arkansas</li><li>California</li><li>Colorado</li><li>Connecticut</li><li>Delaware</li><li>District of Columbia</li><li>Florida</li><li>Georgia</li><li>Hawaii</li><li>Idaho</li><li>Illinois</li><li>Indiana</li><li>Iowa</li><li>Kansas</li><li>Kentucky</li></ul>
  <ul class="state-col" style="left:700px"><li>Louisiana</li><li>Maine</li><li>Maryland</li><li>Massachusetts</li><li>Michigan</li><li>Minnesota</li><li>Mississippi</li><li>Missouri</li><li>Montana</li><li>Nebraska</li><li>Nevada</li><li>New Hampshire</li><li>New Jersey</li><li>New Mexico</li><li>New York</li><li>North Carolina</li><li>North Dakota</li></ul>
  <ul class="state-col" style="left:990px"><li>Ohio</li><li>Oklahoma</li><li>Oregon</li><li>Pennsylvania</li><li>Rhode Island</li><li>South Carolina</li><li>South Dakota</li><li>Tennessee</li><li>Texas</li><li>Utah</li><li>Vermont</li><li>Virginia</li><li>Washington</li><li>West Virginia</li><li>Wisconsin</li><li>Wyoming</li></ul>
</section>

<section class="advisor">
  <div class="advisor-photo" role="img" aria-label="Senior man with arms outstretched against a bright sky"></div>
  <h2>Your local advisor.<em>You decide.</em></h2>
  <p class="lead">Over 400 senior advisors across the U.S. and Canada are ready to help your family with:</p>
  <ul>
    <li><svg width="24" height="24" viewBox="0 0 24 24" fill="#1d2566"><path d="M12 2a7 7 0 0 0-7 7c0 5 7 13 7 13s7-8 7-13a7 7 0 0 0-7-7zm0 9.5A2.5 2.5 0 1 1 12 6.5a2.5 2.5 0 0 1 0 5z"/></svg>Insider's tips for the area near you</li>
    <li><svg width="24" height="24" viewBox="0 0 24 24" fill="#1d2566"><path d="M3 4h18v12H8l-5 4z"/></svg>Advice tailored to your unique situation</li>
    <li><svg width="24" height="24" viewBox="0 0 24 24" fill="none" stroke="#1d2566" stroke-width="2"><circle cx="12" cy="12" r="9"/><path d="M12 7v6M12 16v1"/></svg>Time saving know-how and resources</li>
  </ul>
</section>

<section class="city-links">
  <div class="city-col" style="left:95px"><h3>Independent Living</h3><ul><li>New York Independent Living</li><li>Los Angeles Independent Living</li><li>Chicago Independent Living</li><li>Dallas Independent Living</li><li>Houston Independent Living</li><li>Washington DC Independent Living</li><li>Philadelphia Independent Living</li><li>Miami Independent Living</li><li>Atlanta Independent Living</li><li>Boston Independent Living</li><li>San Francisco Independent Living</li><li>Phoenix Independent Living</li><li>Orange County Independent Living</li><li>Detroit Independent Living</li><li>Seattle Independent Living</li><li>Minneapolis Independent Living</li><li>San Diego Independent Living</li><li>Tampa Independent Living</li><li>Denver Independent Living</li><li>St. Louis Independent Living</li><li>Baltimore Independent Living</li></ul></div>
  <div class="city-col" style="left:500px"><h3>Memory <span style="color:var(--green)">Care</span></h3><ul><li>New York Memory Care</li><li>Los Angeles Memory Care</li><li>Chicago Memory Care</li><li>Dallas Memory Care</li><li>Houston Memory Care</li><li>Washington DC Memory Care</li><li>Philadelphia Memory Care</li><li>Miami Memory Care</li><li>Atlanta Memory Care</li><li>Boston Memory Care</li><li>San Francisco Memory Care</li><li>Phoenix Memory Care</li><li>Orange County Memory Care</li><li>Detroit Memory Care</li><li>Seattle Memory Care</li><li>Minneapolis Memory Care</li><li>San Diego Memory Care</li><li>Tampa Memory Care</li><li>Denver Memory Care</li><li>St. Louis Memory Care</li><li>Baltimore Memory Care</li></ul></div>
  <div class="city-col" style="left:870px"><h3>Nursing Homes</h3><ul><li>New York Nursing Homes</li><li>Los Angeles Nursing Homes</li><li>Chicago Nursing Homes</li><li>Dallas Nursing Homes</li><li>Houston Nursing Homes</li><li>Washington DC Nursing Homes</li><li>Philadelphia Nursing Homes</li><li>Miami Nursing Homes</li><li>Atlanta Nursing Homes</li><li>Boston Nursing Homes</li><li>San Francisco Nursing Homes</li><li>Phoenix Nursing Homes</li><li>Orange County Nursing Homes</li><li>Detroit Nursing Homes</li><li>Seattle Nursing Homes</li><li>Minneapolis Nursing Homes</li><li>San Diego Nursing Homes</li><li>Tampa Nursing Homes</li><li>Denver Nursing Homes</li><li>St. Louis Nursing Homes</li><li>Baltimore Nursing Homes</li></ul></div>
</section>

<footer class="site-footer">
  <div class="brand"><span class="brand-dot"></span><span class="brand-name">The Elder Nook</span></div>
  <div class="brand-tag">CONNECTING FAMILIES TO SENIOR LIVING</div>
  <div class="foot-col" style="left:205px"><h4>ABOUT THE ELDER NOOK</h4><p>Lorem ipsum dolor sit amet, con sectetuer adipiscing elit, sed diam nonummy nibh euismod tincidunt ut laoreet dolore magna aliquam erat volutpat. Ut wisi enim ad minim veniam.</p></div>
  <div class="foot-col" style="left:505px"><h4>QUICK LINKS</h4><ul><li>Assisted Living</li><li>Memory Care</li><li>Nursing Homes</li><li>More Living Options</li><li>Planning &amp; Advice</li><li>Our Service Works</li></ul></div>
  <div class="foot-phone">
    <span class="phone-ring"><svg width="26" height="26" viewBox="0 0 24 24"><path d="M6.6 10.8a15 15 0 0 0 6.6 6.6l2.2-2.2a1 1 0 0 1 1-.25 11.4 11.4 0 0 0 3.6.57 1 1 0 0 1 1 1V20a1 1 0 0 1-1 1A17 17 0 0 1 3 4a1 1 0 0 1 1-1h3.5a1 1 0 0 1 1 1c0 1.25.2 2.45.57 3.6a1 1 0 0 1-.25 1z" fill="#fff"/></svg></span>
    <div><strong>1-800-555-0142</strong><small>Call Today to a Local Advisor for FREE</small></div>
  </div>
  <div class="socials"><span></span><span></span><span></span></div>
</footer>

<div class="copyright abs" style="left:0;width:1200px">COPYRIGHT © 2024 THE ELDER NOOK. ALL RIGHTS RESERVED.</div>

</body>
</html>
```